Website - Loretta Dubrow

I need a website that has multiple pages and easy for me to update pictures, content and blogs as an ongoing basis’s.
It will have videos and needs to be compatible to view easily and aesthetically on mobile phones.
Please refer to this website for inspiration www.quinnafernsby.com

Coding

Coded - Design and coding required

Number of Pages Required

5+ page

Other font styles liked:
• Refer to website provided as inspiration

Requirements
Must have
• Please use stock images for now to do design, but I will be providing all imagery, videos and content

```html
<!DOCTYPE html>
<html lang="en">
<head>
<meta charset="utf-8">
<title>Loretta Dubrow</title>
<link rel="stylesheet" href="https://fonts.googleapis.com/css2?family=Roboto:wght@400;500;700&family=Montserrat:wght@400&display=swap">
<style>
:root{
  --ink:#111111;
  --white:#ffffff;
  --hero-blue:#4f7d90;
  --hero-blue-dark:#3f6a7c;
  --text-grey:#333333;
  --muted:#555555;
  --footer:#141414;
  --dusk-top:#2a2a33;
  --dusk-glow:#d4622a;
}
*{box-sizing:border-box;margin:0;padding:0}
html,body{width:1200px;height:2932px;overflow:hidden}
body{position:relative;font-family:'Roboto',sans-serif;color:var(--ink);background:var(--white)}
.abs{position:absolute}

/* hero */
.hero{position:absolute;left:0;top:0;width:1200px;height:600px;background:linear-gradient(180deg,#5a8799 0%,var(--hero-blue) 55%,var(--hero-blue-dark) 100%);overflow:hidden}
.hero-photo{position:absolute;left:600px;top:60px;width:480px;height:540px;background:radial-gradient(ellipse at 45% 45%,#c9977c 0%,#a87560 45%,rgba(79,125,144,0) 75%)}
.hero-ridge{position:absolute;left:0;top:300px;width:1200px;height:300px;background:linear-gradient(180deg,rgba(80,120,135,0) 0%,rgba(60,100,115,.5) 100%)}
.logo{position:absolute;left:112px;top:32px;font-size:28px;font-weight:500;color:var(--white);letter-spacing:.2px}
.nav{position:absolute;top:38px;display:flex;font-size:16px;font-weight:500;color:var(--white)}
.nav span{position:absolute;white-space:nowrap}
.social-ring{position:absolute;border:1.5px solid var(--white);border-radius:50%}
.hero-title{position:absolute;left:135px;top:236px;font-size:46px;font-weight:700;line-height:48px;color:var(--white)}
.btn-dark{position:absolute;background:var(--ink);color:var(--white);font-weight:500;display:flex;align-items:center;justify-content:center}
.dots{position:absolute;top:553px;left:561px;display:flex;gap:9px}
.dots i{width:12px;height:12px;border-radius:50%;background:rgba(255,255,255,.6)}
.dots i:first-child{background:var(--white)}

/* about */
.about-frame{position:absolute;left:143px;top:668px;width:408px;height:482px;border:3px solid var(--ink)}
.about-photo{position:absolute;left:160px;top:685px;width:408px;height:483px;background:linear-gradient(180deg,#8aa3b8 0%,#5f7583 30%,#7c7a78 60%,#d85aa6 75%,#5a5452 100%)}
.about-title{position:absolute;left:620px;top:760px;font-size:38px;font-weight:700}
.about-rule{position:absolute;left:620px;top:810px;width:86px;height:4px;background:#444}
.about-text{position:absolute;left:620px;top:833px;width:440px;font-size:13.5px;line-height:28.4px;color:var(--text-grey)}

/* video band */
.video-band{position:absolute;left:0;top:1238px;width:1200px;height:520px;background:#2a2a2a}
.video-side{position:absolute;top:0;height:520px;background:linear-gradient(180deg,#6a605a,#2c2826)}
.video-main{position:absolute;left:158px;top:0;width:893px;height:520px;background:linear-gradient(180deg,#3a2a30 0%,#cfc8c4 25%,#a89088 55%,#2a2626 100%)}
.video-shade{position:absolute;left:158px;top:260px;width:893px;height:260px;background:linear-gradient(180deg,rgba(0,0,0,0),rgba(0,0,0,.45))}
.slide-arrow{position:absolute;top:242px;width:34px;height:36px;background:#d9d9d9;display:flex;align-items:center;justify-content:center}
.video-caption{position:absolute;left:228px;top:346px;font-size:21px;font-weight:700;line-height:34px;color:var(--white)}
.btn-video{position:absolute;left:227px;top:430px;width:187px;height:57px;border:1.5px solid var(--white);background:var(--ink);color:var(--white);font-size:17px;font-weight:700;display:flex;align-items:center;justify-content:center;gap:8px}

/* blog */
.blog-title{position:absolute;left:0;top:1832px;width:1200px;text-align:center;font-size:44px;font-weight:700}
.card{position:absolute;top:1903px;width:304px;height:429px;background:var(--white);box-shadow:0 2px 8px rgba(0,0,0,.12)}
.card-img{position:absolute;left:0;top:0;width:304px;height:220px}
.card-date{position:absolute;left:80px;top:200px;width:144px;height:40px;background:var(--ink);color:var(--white);font-size:14px;font-weight:700;display:flex;align-items:center;justify-content:center}
.card-title{position:absolute;left:22px;top:260px;width:270px;font-size:20px;font-weight:500;line-height:26px}
.card-text{position:absolute;left:20px;top:321px;width:270px;font-size:13.5px;line-height:25px;color:var(--muted)}
.card-more{position:absolute;left:20px;top:399px;font-size:15px;font-weight:500;display:flex;align-items:center;gap:12px}
.card-more i{display:block;width:40px;height:1.5px;background:var(--ink)}

/* newsletter */
.touch{position:absolute;left:0;top:2417px;width:1200px;height:400px;background:linear-gradient(180deg,var(--dusk-top) 0%,#4a3236 18%,#a5472a 32%,var(--dusk-glow) 40%,#6a2e22 52%,#1c1418 70%,#0e0d10 100%)}
.touch-title{position:absolute;left:0;top:90px;width:1200px;text-align:center;font-size:38px;font-weight:700;color:var(--white)}
.touch-sub{position:absolute;left:0;top:137px;width:1200px;text-align:center;font-size:18px;color:#f3e3d8}
.field{position:absolute;top:181px;width:228px;height:49px;background:var(--white);font-size:14px;color:#555;padding-left:16px;display:flex;align-items:center}
.btn-signup{position:absolute;left:516px;top:262px;width:169px;height:51px;border:2px solid var(--white);color:var(--white);font-size:17px;font-weight:500;display:flex;align-items:center;justify-content:center}

/* footer */
.footer{position:absolute;left:0;top:2817px;width:1200px;height:115px;background:var(--footer);color:var(--white)}
.foot-nav span{position:absolute;top:42px;font-size:15px;font-weight:700}
.copyright{position:absolute;left:111px;top:76px;font-family:'Montserrat',sans-serif;font-size:14px}
.foot-ring{position:absolute;top:29px;width:42px;height:42px;border:2px solid var(--white);border-radius:50%}
</style>
</head>
<body>

<header class="hero">
  <div class="hero-ridge"></div>
  <div class="hero-photo" role="img" aria-label="Portrait of a woman holding a fruit smoothie"></div>
  <div class="logo">LORETTA DUBROW</div>
  <nav class="nav">
    <span style="left:506px">HOME</span>
    <span style="left:601px">ABOUT</span>
    <span style="left:701px">BLOG</span>
    <span style="left:791px">STORIES</span>
    <span style="left:904px">CONTACT</span>
  </nav>
  <div class="social-ring" style="left:1007px;top:29px;width:37px;height:37px" aria-label="Social link"></div>
  <div class="social-ring" style="left:1051px;top:29px;width:37px;height:37px" aria-label="Social link"></div>
  <h1 class="hero-title">BE BOLD BE BRAVE<br>BE YOURSELF</h1>
  <div class="btn-dark" style="left:137px;top:364px;width:153px;height:43px;font-size:16px">GET STARTED</div>
  <svg class="abs" style="left:72px;top:283px" width="20" height="34" viewBox="0 0 20 34"><path d="M18 2 3 17l15 15" fill="none" stroke="#fff" stroke-width="2"/></svg>
  <svg class="abs" style="left:1108px;top:283px" width="20" height="34" viewBox="0 0 20 34"><path d="M2 2l15 15L2 32" fill="none" stroke="#fff" stroke-width="2"/></svg>
  <div class="dots"><i></i><i></i><i></i><i></i></div>
</header>

<section>
  <div class="about-frame"></div>
  <div class="about-photo" role="img" aria-label="Woman in a pink dress on a lakeside jetty"></div>
  <h2 class="about-title">ABOUT US</h2>
  <div class="about-rule"></div>
  <p class="about-text">Lorem ipsum dolor sit amet, consectetu elit, eiusmod tempor incididunt ut labore et dolore magna al ipsum suspendisse ultrices gravida. Risus commodo viverra maecenas accumsan lacus vel facilisis. Lorem ipsum dolor sit amet, consectetu elit, eiusmod tempor incididunt ut labore et dolore magna al ipsum suspendisse ultrices gravida. Risus commodo viverra maecenas accumsan lacus vel facilisis.</p>
  <div class="btn-dark" style="left:620px;top:1022px;width:144px;height:47px;font-size:15px">LEARN MORE</div>
</section>

<section class="video-band">
  <div class="video-side" style="left:0;width:158px" role="img" aria-label="Dance studio still"></div>
  <div class="video-side" style="left:1051px;width:149px" role="img" aria-label="Dance studio still"></div>
  <div class="video-main" role="img" aria-label="Dancers rehearsing in a studio"></div>
  <div class="video-shade"></div>
  <div class="slide-arrow" style="left:5px"><svg width="12" height="20" viewBox="0 0 12 20"><path d="M10 2 2 10l8 8" fill="none" stroke="#333" stroke-width="1.5"/></svg></div>
  <div class="slide-arrow" style="left:1170px"><svg width="12" height="20" viewBox="0 0 12 20"><path d="M2 2l8 8-8 8" fill="none" stroke="#333" stroke-width="1.5"/></svg></div>
  <p class="video-caption">The standard Lorem Ipsum passage,<br>used since the 1500s</p>
  <div class="btn-video"><svg width="11" height="12" viewBox="0 0 11 12"><path d="M0 0l11 6-11 6z" fill="#fff"/></svg>WATCH VIDEO</div>
</section>

<section>
  <h2 class="blog-title">LATEST BLOG</h2>
  <article class="card" style="left:112px">
    <div class="card-img" role="img" aria-label="Woman seated on a kitchen counter" style="background:linear-gradient(180deg,#e8e4de,#b9b6c4 60%,#d8d4cc)"></div>
    <div class="card-date">MAY 21, 2019</div>
    <h3 class="card-title">The standard Lorem Ipsum passage, used sin 1500s</h3>
    <p class="card-text">Sed ut perspiciatis unde omnis iste natus error sit voluptatem aantium doloremque laudantium, totam rem aperiam</p>
    <div class="card-more"><i></i>Read More</div>
  </article>
  <article class="card" style="left:448px">
    <div class="card-img" role="img" aria-label="Skincare routine selfie" style="background:linear-gradient(135deg,#3e2e24,#8a6048 50%,#7d5aa8)"></div>
    <div class="card-date">MAR 2, 2021</div>
    <h3 class="card-title">The standard Lorem Ipsum passage, used sin 1500s</h3>
    <p class="card-text">Sed ut perspiciatis unde omnis iste natus error sit voluptatem aantium doloremque laudantium, totam rem aperiam</p>
    <div class="card-more"><i></i>Read More</div>
  </article>
  <article class="card" style="left:784px">
    <div class="card-img" role="img" aria-label="Portrait holding a smoothie" style="background:linear-gradient(135deg,#7ab8c8,#b88a70 55%,#d86a58)"></div>
    <div class="card-date">JAN 4, 2021</div>
    <h3 class="card-title">The standard Lorem Ipsum passage, used sin 1500s</h3>
    <p class="card-text">Sed ut perspiciatis unde omnis iste natus error sit voluptatem aantium doloremque laudantium, totam rem aperiam</p>
    <div class="card-more"><i></i>Read More</div>
  </article>
</section>

<section class="touch" role="img" aria-label="Sunset over a lake with mountain silhouettes">
  <h2 class="touch-title">STAY IN TOUCH</h2>
  <p class="touch-sub">Receive News &amp; Offerings</p>
  <div class="field" style="left:246px">First Name</div>
  <div class="field" style="left:486px">Last Name</div>
  <div class="field" style="left:727px">Email</div>
  <div class="btn-signup">SIGN UP</div>
</section>

<footer class="footer">
  <div class="foot-nav">
    <span style="left:111px">HOME</span>
    <span style="left:196px">ABOUT</span>
    <span style="left:287px">BLOG</span>
    <span style="left:367px">STORIES</span>
    <span style="left:469px">CONTACT</span>
  </div>
  <p class="copyright">2021 Loretta Dubrow | All Rights Reserved.</p>
  <div class="foot-ring" style="left:934px" aria-label="Social link"></div>
  <div class="foot-ring" style="left:985px" aria-label="Social link"></div>
  <div class="foot-ring" style="left:1037px" aria-label="Social link"></div>
</footer>

</body>
</html>
```